Email signature and business card

Australian company called Brakmere. We provide construction and maintenance services to the mining industry. I would like the design to be similar to our website theme(www.brakmere.com.au) whilst staying compact. RGB colours to include: 42,96,140 and 232,163,0 and I have attached 2 logos.

The following fields will need to be included:

Full Name
Title
Location/Project
Phone
Mobile
Fax
Email
Web site

Target Market(s)

Mining Industry

Industry/Entity Type

Construction

Requirements
Must have
• Full Name, Title, Office Address, Phone, Mobile, Fax, Email, Web address
• Back of card must include: Boilermaking, Carpentry, Concrete, Construction, Cranes, Data and Comms, Electrical, Fabrication, Fitting, Labour Hire, Plumbing, Rigging, Shutdowns

```html
<!DOCTYPE html>
<html lang="en">
<head>
<meta charset="utf-8">
<title>Brakmere – Email Signature</title>
<link href="https://fonts.googleapis.com/css2?family=Satisfy&family=Open+Sans:wght@400;700&family=Arimo:wght@400;700&display=swap" rel="stylesheet">
<style>
  :root {
    --teal: #0c5d80;
    --gold: #f2b400;
    --ink: #1d1d1d;
    --paper: #ffffff;
    --bg-light: #dedede;
    --bg-dark: #a9a9a9;
  }
  * { margin: 0; padding: 0; box-sizing: border-box; }
  html, body { width: 1200px; height: 1200px; overflow: hidden; }
  body {
    position: relative;
    background: radial-gradient(ellipse at 50% 48%, var(--bg-light) 0%, #cfcfcf 45%, var(--bg-dark) 100%);
    font-family: "Open Sans", sans-serif;
  }
  .board-title {
    position: absolute;
    top: 238px; left: 0; width: 1200px;
    text-align: center;
    font-family: "Arimo", sans-serif;
    font-weight: 700;
    font-size: 39px;
    letter-spacing: 1px;
    color: var(--teal);
  }
  .signature {
    position: absolute;
    left: 193px; top: 391px;
    width: 780px; height: 387px;
    background: var(--paper);
    box-shadow: 0 4px 14px rgba(0,0,0,0.45);
  }
  .brand {
    position: absolute;
    left: 39px; top: 50px;
    width: 200px; height: 245px;
    display: flex; align-items: center; gap: 10px;
  }
  .brand-square {
    width: 18px; height: 18px;
    background: var(--gold);
    flex: none;
  }
  .brand-name {
    font-family: "Open Sans", sans-serif;
    font-weight: 700;
    font-size: 26px;
    color: var(--teal);
  }
  .details {
    position: absolute;
    left: 283px; top: 42px;
  }
  .person-name {
    font-family: "Satisfy", cursive;
    font-size: 50px;
    line-height: 60px;
    color: var(--ink);
    letter-spacing: 1px;
  }
  .company {
    margin-top: 17px;
    font-weight: 700;
    font-size: 13px;
    color: var(--teal);
  }
  .address-line {
    margin-top: 8px;
    font-size: 13.5px;
    color: var(--ink);
  }
  .contact-list { list-style: none; margin-top: 2px; }
  .contact-item {
    display: flex; align-items: center;
    height: 26.5px;
    font-size: 13.5px;
    color: var(--ink);
  }
  .contact-icon { width: 20px; height: 18px; margin-right: 15px; }
  .contact-icon * { fill: none; stroke: var(--gold); stroke-width: 1.8; }
  .connect {
    position: absolute;
    left: 39px; top: 329px;
    display: flex; align-items: center;
  }
  .connect-label {
    font-family: "Arimo", sans-serif;
    font-size: 18px;
    color: var(--teal);
    width: 135px;
  }
  .social-links { display: flex; gap: 11px; list-style: none; }
  .social-dot {
    width: 34px; height: 34px;
    border-radius: 50%;
    background: var(--teal);
  }
</style>
</head>
<body>
  <h1 class="board-title">Email Signature</h1>

  <section class="signature">
    <div class="brand">
      <span class="brand-square"></span>
      <span class="brand-name">Brakmere</span>
    </div>

    <div class="details">
      <p class="person-name">Lena Marsh</p>
      <p class="company">Brakmere. Inc</p>
      <p class="address-line">Hollenweg 14</p>
      <p class="address-line">CH - 6405 Felsbach</p>
      <ul class="contact-list">
        <li class="contact-item">
          <svg class="contact-icon" viewBox="0 0 20 18"><path d="M3 7 Q10 1 17 7 L15 9 L13 7 L7 7 L5 9 Z"/><rect x="5" y="10" width="10" height="6" rx="2"/></svg>
          041 628 14 20
        </li>
        <li class="contact-item">
          <svg class="contact-icon" viewBox="0 0 20 18"><rect x="6" y="1" width="8" height="16" rx="1.5"/><line x1="9" y1="14" x2="11" y2="14"/></svg>
          041 628 14 20
        </li>
        <li class="contact-item">
          <svg class="contact-icon" viewBox="0 0 20 18"><rect x="6" y="1" width="8" height="5"/><rect x="2" y="6" width="16" height="7" rx="1"/><rect x="6" y="11" width="8" height="6"/></svg>
          041 628 14 22
        </li>
        <li class="contact-item">
          <svg class="contact-icon" viewBox="0 0 20 18"><rect x="2" y="4" width="16" height="11"/><path d="M2 4 L10 11 L18 4"/></svg>
          lena@brakmere.com
        </li>
      </ul>
    </div>

    <div class="connect">
      <span class="connect-label">Contact Me</span>
      <ul class="social-links">
        <li class="social-dot" role="img" aria-label="Social profile link"></li>
        <li class="social-dot" role="img" aria-label="Social profile link"></li>
        <li class="social-dot" role="img" aria-label="Video channel link"></li>
        <li class="social-dot" role="img" aria-label="Professional network link"></li>
      </ul>
    </div>
  </section>
</body>
</html>
```